Private lender of mortgages and rent to own housing

need a website that reflects real estate especially mortgage lending and rent to own houses..
Sections as follows
Home About Types of mortgages Rent to own Contact us
Target Market(s)
consumers who require non traditonal mortgages
Industry/Entity Type
Mortgage
Coding
Coded - Design and coding required
Number of Pages Required
4 page
Font styles to use
Sans Serif
Colors
Designer to choose colors to be used in the design.
Requirements
Must have
- background pictures on pages. with nice picture on homepage of houses or a community
Nice to have
- contact us form i supplied a ink to

```html
<!DOCTYPE html>
<html lang="en">
<head>
<meta charset="utf-8">
<title>Harbourline Lending Group</title>
<link href="https://fonts.googleapis.com/css2?family=Open+Sans:wght@300;400;600;700&family=Raleway:wght@300;700;800&display=swap" rel="stylesheet">
<style>
  :root {
    --navy: #2c2a6e;
    --navy-dark: #1f1d52;
    --ink: #333344;
    --muted: #777788;
    --footer: #2a2a33;
    --footer-text: #b9b9c4;
    --white: #ffffff;
  }
  * { margin: 0; padding: 0; box-sizing: border-box; }
  html, body { width: 675px; height: 1200px; overflow: hidden; }
  body { font-family: "Open Sans", Arial, sans-serif; color: var(--ink); background: var(--white); position: relative; }

  .site-header { position: absolute; top: 0; left: 0; width: 675px; height: 50px; background: var(--white); display: flex; align-items: center; justify-content: space-between; padding: 0 40px; }
  .brand { display: flex; align-items: center; gap: 7px; font-weight: 700; font-size: 10px; color: var(--navy); letter-spacing: .5px; }
  .brand-mark { width: 14px; height: 14px; background: var(--navy); }
  .main-nav { display: flex; gap: 16px; font-size: 7px; font-weight: 600; letter-spacing: .4px; }
  .main-nav a { color: var(--muted); text-decoration: none; padding: 4px 0; }
  .main-nav a.active { color: var(--navy); border-bottom: 1.5px solid var(--navy); }

  .hero { position: absolute; top: 50px; left: 0; width: 675px; height: 355px;
    background: linear-gradient(100deg, #6f7a8c 0%, #b7bcc6 35%, #d6d2cc 60%, #a89a8c 100%); }
  .hero-overlay { position: absolute; inset: 0; background: linear-gradient(180deg, rgba(30,30,60,.05) 0%, rgba(30,30,60,.35) 100%); }
  .hero-title { position: absolute; left: 56px; top: 146px; font-family: "Raleway", Arial, sans-serif; font-size: 27px; line-height: 34px; color: var(--white); letter-spacing: .8px; white-space: nowrap; }
  .hero-title b { font-weight: 800; }
  .hero-title span { font-weight: 300; }
  .hero-dots { position: absolute; left: 58px; top: 188px; display: flex; gap: 5px; }
  .hero-dots i { width: 5px; height: 5px; border-radius: 50%; background: var(--navy); display: block; }
  .hero-dots i:first-child { background: var(--white); }

  .section-title { font-family: "Raleway", Arial, sans-serif; font-weight: 800; color: var(--navy); font-size: 19px; text-align: center; letter-spacing: .5px; }
  .title-rule { width: 40px; height: 2px; background: var(--navy); margin: 5px auto 0; }
  .btn { display: inline-block; background: var(--navy); color: var(--white); font-size: 6px; font-weight: 700; letter-spacing: .5px; padding: 5px 9px; text-decoration: none; }

  .rent-own { position: absolute; top: 428px; left: 0; width: 675px; text-align: center; }
  .rent-own .subtitle { font-size: 10px; color: var(--muted); margin-top: 4px; }
  .rent-own p { width: 560px; margin: 20px auto 0; font-size: 6.5px; line-height: 12px; color: var(--muted); }
  .rent-own .btn { margin-top: 40px; }

  .process { position: absolute; top: 637px; left: 0; width: 675px; height: 274px; }
  .process-bg { position: absolute; inset: 0; background: linear-gradient(90deg, #dcdde2 0%, #ecebea 45%, #d9d5cf 100%); }
  .process-fade { position: absolute; inset: 0; background: rgba(255,255,255,.7); }
  .process .section-title { position: absolute; top: 22px; width: 100%; }
  .process .title-rule { position: absolute; top: 48px; left: 317px; margin: 0; }
  .steps { position: absolute; top: 78px; left: 45px; width: 585px; display: flex; justify-content: space-between; }
  .step { width: 130px; text-align: center; }
  .step svg { display: block; margin: 0 auto; }
  .step h3 { font-size: 9.5px; font-weight: 700; color: var(--navy-dark); margin-top: 14px; letter-spacing: .3px; }
  .step p { font-size: 6.5px; line-height: 10px; color: var(--muted); margin-top: 6px; height: 40px; }
  .step .btn { margin-top: 8px; }

  .testimonials { position: absolute; top: 932px; left: 0; width: 675px; text-align: center; }
  .testimonials .intro { width: 480px; margin: 12px auto 0; font-size: 6.5px; line-height: 10px; color: #a0a0ac; }
  .quotes { display: flex; justify-content: center; gap: 95px; margin-top: 32px; }
  .quote { display: flex; align-items: center; gap: 10px; text-align: left; width: 190px; }
  .avatar { width: 42px; height: 42px; border-radius: 50%; background: linear-gradient(135deg, #e8d8cc, #b89e8c); flex: none; }
  .quote h4 { font-size: 6.5px; font-weight: 700; color: var(--navy); }
  .quote .date { font-size: 5.5px; color: #a0a0ac; margin-top: 2px; }
  .quote p { font-size: 5.5px; line-height: 8px; color: var(--muted); margin-top: 3px; }
  .arrow { position: absolute; top: 1080px; font-size: 14px; color: #b0b0ba; }

  .site-footer { position: absolute; top: 1143px; left: 0; width: 675px; height: 57px; background: var(--footer); padding: 14px 40px 0; }
  .footer-nav { display: flex; gap: 11px; font-size: 6px; color: var(--footer-text); letter-spacing: .3px; }
  .copyright { font-size: 5.5px; color: #8a8a96; margin-top: 7px; }
  .connect { position: absolute; right: 56px; top: 17px; display: flex; align-items: center; gap: 4px; font-size: 6px; color: var(--footer-text); }
  .connect span { margin-right: 5px; }
  .connect i { width: 12px; height: 12px; border-radius: 50%; display: block; }
  .to-top { position: absolute; right: 30px; top: 19px; width: 10px; height: 10px; background: #44444f; }
</style>
</head>
<body>

<header class="site-header">
  <div class="brand"><span class="brand-mark"></span>HARBOURLINE LENDING GROUP</div>
  <nav class="main-nav">
    <a class="active" href="#">HOME</a>
    <a href="#">ABOUT</a>
    <a href="#">TYPES OF MORTGAGES</a>
    <a href="#">RENT TO OWN</a>
    <a href="#">CONTACT US</a>
  </nav>
</header>

<section class="hero" role="img" aria-label="Photo of a handshake across a desk with documents, sealing a home loan agreement">
  <div class="hero-overlay"></div>
  <h1 class="hero-title"><b>HARBOURLINE</b> <span>LENDING GROUP</span></h1>
  <div class="hero-dots"><i></i><i></i><i></i></div>
</section>

<section class="rent-own">
  <h2 class="section-title">RENT TO OWN A HOME</h2>
  <div class="subtitle">We Can Put You In Your Own Home Today</div>
  <p>We know life sometimes delivers challenges and it can be hard to get back on track once your home dreams have been set aside. Maybe you have been through a divorce, a job change, a move to a new town, or simply a credit score that does not tell the whole story. Our rent to own program gives you the chance to live in the home you want today while you rebuild your credit and save toward ownership. Let us walk you through every step so you can plan for the future with confidence.</p>
  <a class="btn" href="#">READ MORE &rsaquo;</a>
</section>

<section class="process">
  <div class="process-bg" role="img" aria-label="Faded background photo of a residential street"></div>
  <div class="process-fade"></div>
  <h2 class="section-title">OUR PROCESS</h2>
  <div class="title-rule"></div>
  <div class="steps">
    <div class="step">
      <svg width="70" height="40" viewBox="0 0 70 40"><path d="M4 36 L35 8 L66 36" fill="none" stroke="#2c2a6e" stroke-width="6"/><rect x="48" y="10" width="6" height="12" fill="#2c2a6e"/></svg>
      <h3>DOWN PAYMENT</h3>
      <p>We require a minimum down payment of 5% to 10% of the purchase price of the home you want to buy.</p>
      <a class="btn" href="#">READ MORE &rsaquo;</a>
    </div>
    <div class="step">
      <svg width="70" height="40" viewBox="0 0 70 40"><path d="M4 36 L35 8 L66 36" fill="none" stroke="#2c2a6e" stroke-width="6"/><rect x="48" y="10" width="6" height="12" fill="#2c2a6e"/></svg>
      <h3>HOUSEHOLD INCOME</h3>
      <p>Stable, provable household income that can support the price of the home you would like to purchase.</p>
      <a class="btn" href="#">READ MORE &rsaquo;</a>
    </div>
    <div class="step">
      <svg width="70" height="40" viewBox="0 0 70 40"><path d="M4 36 L35 8 L66 36" fill="none" stroke="#2c2a6e" stroke-width="6"/><rect x="48" y="10" width="6" height="12" fill="#2c2a6e"/></svg>
      <h3>CREDIT REPORT</h3>
      <p>Although your credit does not need to be perfect, we review it to understand your situation.</p>
      <a class="btn" href="#">READ MORE &rsaquo;</a>
    </div>
    <div class="step">
      <svg width="70" height="40" viewBox="0 0 70 40"><path d="M4 36 L35 8 L66 36" fill="none" stroke="#2c2a6e" stroke-width="6"/><rect x="48" y="10" width="6" height="12" fill="#2c2a6e"/></svg>
      <h3>SELECTING A HOUSE</h3>
      <p>Pick the house that suits your family and we arrange the terms that get you started.</p>
      <a class="btn" href="#">READ MORE &rsaquo;</a>
    </div>
  </div>
</section>

<section class="testimonials">
  <h2 class="section-title">TESTIMONIALS</h2>
  <div class="title-rule"></div>
  <p class="intro">We love to hear from the families we have helped into a home. Here is what a few of our clients have to say about working with us.</p>
  <div class="quotes">
    <div class="quote">
      <div class="avatar" role="img" aria-label="Client portrait"></div>
      <div>
        <h4>MARIA ELLEN STONE</h4>
        <div class="date">Posted on 08 Sep 2017</div>
        <p>The team made the whole process simple and we moved in sooner than expected.</p>
      </div>
    </div>
    <div class="quote">
      <div class="avatar" role="img" aria-label="Client portrait"></div>
      <div>
        <h4>DANIEL R. PIKE</h4>
        <div class="date">Posted on 08 Sep 2017</div>
        <p>Honest advice and fair terms helped us finally own the house we love.</p>
      </div>
    </div>
  </div>
</section>
<div class="arrow" style="left:34px">&lsaquo;</div>
<div class="arrow" style="right:34px">&rsaquo;</div>

<footer class="site-footer">
  <nav class="footer-nav"><span>HOME</span><span>ABOUT</span><span>TYPES OF MORTGAGES</span><span>RENT TO OWN</span><span>CONTACT US</span></nav>
  <div class="copyright">Copyright &copy; 2017 Harbourline Lending Group. All Rights Reserved.</div>
  <div class="connect"><span>CONNECT US</span><i style="background:#3b5998"></i><i style="background:#1da1f2"></i><i style="background:#dd4b39"></i><i style="background:#e8a33d"></i><i style="background:#cb2027"></i></div>
  <div class="to-top"></div>
</footer>

</body>
</html>
```